I need a sophisticated and powerful book cover design that combines Japanese minimalism with contemporary appeal. The cover should convey personal transformation through the metaphor of a katana (Japanese sword).
Key Design Elements:
A katana, either partially shown or artistically rendered
Subtle Japanese design elements without being stereotypical
Clean, minimalist aesthetic
Professional font selection that bridges Eastern and Western typography
Color scheme: Deep blacks, steel grays, and possibly a touch of red or gold for accent
Mood/Style:
Professional and sophisticated
Blend of traditional Japanese aesthetics with modern design
Should appeal to personal development and business readers
Must convey strength and transformation
Elegant rather than aggressive
Specific Requirements:
Title: "The Lantern Compass"
Subtitle: "Quiet Methods for Growing Inner Steadiness and Calm Endurance"
Author names: Dorvelan Thaske and Meloda Thaske
Cover dimensions: Standard hardcover book size (6" x 9")
Must work well in both physical and digital thumbnail formats
Should be striking and legible when viewed as a small image online
Design Specifics:
Japanese elements such as brushstroke effects, kanji characters, or wave patterns
The design should reflect the book's core message: personal transformation through Japanese wisdom principles, using the katana as a metaphor for growth and development.

```html
<!DOCTYPE html>
<html lang="en">
<head>
<meta charset="utf-8">
<title>The Lantern Compass — Book Cover</title>
<link href="https://fonts.googleapis.com/css2?family=Montserrat:wght@400;500;800;900&display=swap" rel="stylesheet">
<style>
  :root {
    --backdrop: #000000;
    --paper: #ffffff;
    --ink: #111111;
    --accent-red: #e8242a;
    --sun-red-deep: #d8232b;
    --sun-red-light: #ec5a5e;
    --steel-dark: #1c1d24;
    --steel-light: #c9ccd4;
    --blossom: #f6c9d3;
    --blossom-deep: #e892a6;
  }
  * { margin: 0; padding: 0; box-sizing: border-box; }
  html, body {
    width: 1200px; height: 1200px; overflow: hidden;
    background: var(--backdrop);
  }
  .cover {
    position: absolute; left: 240px; top: 60px;
    width: 720px; height: 1080px;
    background: var(--paper);
    overflow: hidden;
    font-family: "Montserrat", sans-serif;
  }
  .sun {
    position: absolute; left: 79px; top: 60px;
    width: 556px; height: 550px; border-radius: 50%;
    background: radial-gradient(circle at 55% 55%, var(--sun-red-light) 0%, var(--sun-red-deep) 75%, var(--sun-red-deep) 100%);
    z-index: 0;
  }
  .blossom-branch {
    position: absolute; left: 0; top: 0;
    width: 130px; height: 176px;
    border-bottom-right-radius: 90px;
    background: linear-gradient(150deg, var(--blossom) 30%, var(--blossom-deep) 100%);
    opacity: 0.85;
    z-index: 0;
  }
  .katana {
    position: absolute; left: 346px; top: 15px;
    width: 28px; height: 822px;
    background: linear-gradient(180deg, var(--steel-dark) 0%, var(--steel-dark) 28%, var(--steel-light) 32%, var(--steel-light) 100%);
    z-index: 1;
  }
  .title-block { position: absolute; inset: 0; z-index: 2; }
  .title {
    position: absolute; left: 0; width: 720px;
    text-align: center; text-transform: uppercase;
    line-height: 1;
  }
  .title-the {
    top: 552px; font-size: 78px; font-weight: 900;
    color: var(--ink); letter-spacing: 10px;
  }
  .title-main {
    font-size: 112px; font-weight: 800;
    color: var(--accent-red); letter-spacing: 2px;
  }
  .title-line-one { top: 622px; }
  .title-line-two { top: 724px; }
  .subtitle {
    position: absolute; left: 40px; width: 640px; top: 850px;
    text-align: center; font-size: 25px; font-weight: 500;
    line-height: 34px; letter-spacing: 1.2px; color: var(--ink);
    z-index: 2;
  }
  .authors {
    position: absolute; left: 0; width: 720px; top: 986px;
    text-align: center; font-size: 35px; font-weight: 400;
    letter-spacing: 1px; color: var(--ink);
    z-index: 2;
  }
</style>
</head>
<body>
  <main class="cover">
    <div class="sun" role="img" aria-label="Red brushstroke sun circle"></div>
    <div class="blossom-branch" role="img" aria-label="Cherry blossom branch"></div>
    <div class="katana" role="img" aria-label="Vertical katana sword with wrapped hilt and gold guard"></div>
    <h1 class="title-block">
      <span class="title title-the">The</span>
      <span class="title title-main title-line-one">Lantern</span>
      <span class="title title-main title-line-two">Compass</span>
    </h1>
    <p class="subtitle">Quiet Methods for Growing Inner<br>Steadiness and Calm<br>Endurance</p>
    <p class="authors">Dorvelan Thaske &amp; Meloda Thaske</p>
  </main>
</body>
</html>
```